New Innovative Counselling and psychotherapy Service needs Business Card design

Keep it simple and professional. On one side, just company name and logo (perhaps in all blue) and maybe a tag line.

On other side (all white) my name and Qualifications in centre

Industry/Entity Type

Health And Wellness

Contact Information for Business Card

Dara Whelby
Counsellor & Psychotherapist
BSc (Psychol.), BA, Dip. (Couns. & Psych.), PG.Cert (CBT), FGTrK, ONRE

I will also require Mobile no, Email and web site address of which I'll pass on to final designer.

Font styles to use
Sans Serif

Requirements
Must have
• My Logo Only and please use the colours in logo that is in it.
Should not have
• Any other images

```html
<!DOCTYPE html>
<html lang="en">
<head>
<meta charset="utf-8">
<title>Clear Harbour – Business Card</title>
<link rel="stylesheet" href="https://fonts.googleapis.com/css2?family=Montserrat:wght@400&family=Work+Sans:wght@400;500&display=swap">
<style>
  :root {
    --bg: #1d1d1f;
    --card: #1a1a1a;
    --card-edge: #262626;
    --pattern-dark: #151515;
    --pattern-light: #3a3a3a;
    --blue: #3fa9e0;
    --green: #7cc242;
    --text: #f2f2f2;
  }
  * { margin: 0; padding: 0; box-sizing: border-box; }
  html, body { width: 1200px; height: 900px; overflow: hidden; }
  body {
    background: var(--bg);
    position: relative;
    font-family: "Work Sans", Arial, sans-serif;
    color: var(--text);
  }
  .card {
    position: absolute;
    left: 280px;
    width: 640px;
    height: 366px;
    background: var(--card);
    border: 1px solid var(--card-edge);
    box-shadow: 0 18px 40px rgba(0,0,0,0.55);
    overflow: hidden;
  }
  .card--back { top: 50px; }
  .card--front { top: 470px; }

  .back-pattern {
    position: absolute;
    inset: 0;
    background: linear-gradient(115deg, var(--pattern-dark) 0%, #222 45%, var(--pattern-light) 100%);
  }
  .back-mark {
    position: absolute;
    left: 452px;
    top: 218px;
    width: 50px;
    height: 50px;
    border-radius: 50%;
    background: var(--blue);
  }

  .brand {
    position: absolute;
    left: 52px;
    top: 150px;
    display: flex;
    align-items: center;
    gap: 18px;
  }
  .brand__dot {
    width: 54px;
    height: 54px;
    border-radius: 50%;
    background: var(--blue);
  }
  .brand__name {
    font-family: "Montserrat", Arial, sans-serif;
    font-weight: 400;
    font-size: 25px;
    letter-spacing: 0.5px;
    color: var(--text);
  }

  .divider {
    position: absolute;
    left: 322px;
    top: 72px;
    width: 2px;
    height: 196px;
    background: var(--green);
  }

  .details {
    position: absolute;
    left: 342px;
    top: 58px;
    width: 290px;
  }
  .details__name {
    font-size: 29px;
    font-weight: 500;
    color: var(--blue);
    letter-spacing: 0.5px;
    line-height: 1.1;
  }
  .details__role,
  .details__quals {
    font-size: 15px;
    line-height: 1.32;
    letter-spacing: 0.3px;
  }
  .contacts {
    list-style: none;
    margin-top: 12px;
    font-size: 16px;
    letter-spacing: 0.3px;
  }
  .contacts li {
    display: flex;
    align-items: center;
    gap: 10px;
    line-height: 1.6;
  }
  .contacts svg { width: 12px; height: 12px; flex: none; }
  .contacts .accent { color: var(--green); }
</style>
</head>
<body>
  <section class="card card--back">
    <div class="back-pattern" role="img" aria-label="Repeating embossed brand-mark pattern"></div>
    <div class="back-mark"></div>
  </section>

  <section class="card card--front">
    <div class="brand">
      <div class="brand__dot"></div>
      <span class="brand__name">ClearHarbour</span>
    </div>

    <div class="divider"></div>

    <div class="details">
      <h1 class="details__name">DARA WHELBY</h1>
      <p class="details__role">Counsellor &amp; Psychotherapist</p>
      <p class="details__quals">BSc (Psychol.), BA, Dip.<br>(Couns. &amp; Psych.), PG.Cert<br>(CBT), FGTrK, ONRE</p>
      <ul class="contacts">
        <li>
          <svg viewBox="0 0 12 12" aria-hidden="true"><path d="M2.5 1 L4.5 1 L5.2 3.4 L4 4.4 Q5 6.8 7.6 8 L8.6 6.8 L11 7.5 L11 9.5 Q10.5 11 9 11 Q1 9.5 1 2.5 Q1 1 2.5 1 Z" fill="var(--blue)"/></svg>
          555-014-2871
        </li>
        <li>
          <svg viewBox="0 0 12 12" aria-hidden="true"><rect x="0.8" y="2.3" width="10.4" height="7.4" fill="none" stroke="var(--blue)" stroke-width="1.1"/><path d="M0.8 2.3 L6 6.6 L11.2 2.3" fill="none" stroke="var(--blue)" stroke-width="1.1"/></svg>
          info@clearharbour.com
        </li>
        <li>
          <svg viewBox="0 0 12 12" aria-hidden="true"><circle cx="6" cy="6" r="5" fill="none" stroke="var(--blue)" stroke-width="1"/><ellipse cx="6" cy="6" rx="2.2" ry="5" fill="none" stroke="var(--blue)" stroke-width="0.9"/><path d="M1 6 H11 M2 3.5 H10 M2 8.5 H10" stroke="var(--blue)" stroke-width="0.8"/></svg>
          <span>www.<span class="accent">clearharbour</span>.com</span>
        </li>
      </ul>
    </div>
  </section>
</body>
</html>
```